Family business needs stationery redesign with new logo

Family owned company, established in 1987 wanting a brand 'refresh'. We are an electrical, refrigeration and construction company based in the Barkly Region Northern Territory, Australia. We have a new logo we would like to use which is uploaded along with our current letterhead and email signature. We are also dropping the word 'contractors' so please do not include this on any designs. Please note also, the 'orange' color used in our logo and designs should be Northern Territory red ochre which is as follows:

RGB (Hex): #C75B12
PantoneĀ® 159 C
CMYK: 1 / 74 / 100 / 7

We are needing our stationery redesigned using our new logo. Please include letterheads, business cards, envelopes, and email signatures.

We currently use our business letterheads for quotations, invoices, letters, HR matters, and internal memos.

We also need a separate simplified letterhead for internal paperwork such as employee leave forms, meeting agendas, and meeting minutes etc.

Reason: Needing more submissions of full package designs. We are wanting all our stationery, including business cards, letterheads, email signatures, envelopes, etc to be cohesive. We also require ALL the information, as supplied on our template letterhead, to be included on the new letterhead designs. including electrical license no.etc Thank you, R&W

Reason: needing more time as work has got in the way of looking over designs. A lot of designs not meeting the brief/criteria.

Industry/Entity Type

Business

Colors
0355a3
f37122

Requirements
Must have
• The 'orange' color used in the designs should be Northern Territory red ochre which is as follows:
• RGB (Hex): #C75B12
• PantoneĀ® 159 C
• CMYK: 1 / 74 / 100 / 7
• ***MUST INCLUDE ALL INFORMATION THAT IS ON OUR CURRENT LETTERHEAD***
Should not have
• Please do not include the word 'contractors'

```html
<!DOCTYPE html>
<html lang="en">
<head>
<meta charset="utf-8">
<title>R&amp;W Business Card</title>
<link rel="stylesheet" href="https://fonts.googleapis.com/css2?family=Arimo:wght@400;700&family=Open+Sans:wght@400&display=swap">
<style>
  :root {
    --navy: #1b2f6d;
    --ochre: #cf5c12;
    --ink: #4a4a4a;
    --rule: #c9c9c9;
    --paper: #ffffff;
    --backdrop: #e7e7e7;
  }
  html, body {
    margin: 0;
    padding: 0;
    width: 1200px;
    height: 987px;
    overflow: hidden;
    background: var(--backdrop);
  }
  .canvas {
    position: relative;
    width: 1200px;
    height: 987px;
  }
  .card {
    position: absolute;
    left: 293px;
    width: 615px;
    height: 352px;
    border-radius: 17px;
    overflow: hidden;
  }
  .card--front { top: 130px; background: var(--paper); }
  .card--back { top: 505px; background: var(--navy); }

  .front-swoosh {
    position: absolute;
    left: 0;
    top: 0;
    width: 615px;
    height: 352px;
  }
  .brand-name {
    position: absolute;
    margin: 0;
    font-family: "Arimo", Arial, sans-serif;
    font-weight: 700;
    line-height: 1;
    text-align: center;
  }
  .card--front .brand-name {
    left: 65px;
    width: 200px;
    top: 152px;
    font-size: 64px;
    color: var(--navy);
  }
  .divider {
    position: absolute;
    left: 314px;
    top: 57px;
    width: 1px;
    height: 232px;
    background: linear-gradient(to bottom, transparent, var(--rule) 15%, var(--rule) 85%, transparent);
  }
  .contact {
    position: absolute;
    left: 355px;
    top: 72px;
    font-family: "Arimo", Arial, sans-serif;
    color: var(--ink);
  }
  .contact__name {
    margin: 0;
    font-size: 22px;
    font-weight: 700;
    color: var(--navy);
    letter-spacing: 0.2px;
  }
  .contact__role {
    margin: 3px 0 0;
    font-size: 17px;
    color: var(--ochre);
  }
  .contact__address {
    margin: 13px 0 0;
    font-size: 16px;
    line-height: 20px;
    font-style: normal;
  }
  .contact__list {
    list-style: none;
    margin: 11px 0 0;
    padding: 0;
    font-size: 16px;
  }
  .contact__list li {
    display: flex;
    align-items: center;
    height: 23.5px;
  }
  .contact__icon {
    width: 14px;
    height: 14px;
    margin-right: 8px;
    fill: var(--navy);
  }
  .card--back .brand-name {
    left: 0;
    width: 615px;
    top: 128px;
    font-size: 96px;
    color: #ffffff;
  }
  .back-web {
    position: absolute;
    left: 0;
    width: 615px;
    top: 302px;
    margin: 0;
    text-align: center;
    font-family: "Open Sans", Arial, sans-serif;
    font-size: 16px;
    letter-spacing: 5px;
    color: #ffffff;
  }
</style>
</head>
<body>
<main class="canvas">
  <section class="card card--front" aria-label="Business card front">
    <svg class="front-swoosh" viewBox="0 0 615 352" aria-hidden="true">
      <path d="M0,258 C210,305 430,320 615,319 L615,323 C430,328 210,318 0,279 Z" fill="var(--ochre)"/>
      <path d="M0,285 C210,322 430,332 615,327 L615,352 L0,352 Z" fill="var(--navy)"/>
    </svg>
    <p class="brand-name">R&amp;W</p>
    <div class="divider"></div>
    <div class="contact">
      <h1 class="contact__name">DANIEL HARPER</h1>
      <p class="contact__role">CEO/Founder</p>
      <address class="contact__address">2140 Ridgeway Road<br>Tennant Creek, NT 0862</address>
      <ul class="contact__list">
        <li>
          <svg class="contact__icon" viewBox="0 0 16 16" aria-hidden="true"><path d="M3.5 1 L6 1 L7 4.5 L5.3 5.8 C6.2 7.8 8.2 9.8 10.2 10.7 L11.5 9 L15 10 L15 12.5 C15 13.9 13.9 15 12.5 15 C6.7 15 1 9.3 1 3.5 C1 2.1 2.1 1 3.5 1 Z"/></svg>
          608 412 7735
        </li>
        <li>
          <svg class="contact__icon" viewBox="0 0 16 16" aria-hidden="true"><path d="M4 1 H12 V5 H4 Z M1 6 H15 V13 H13 V11 H3 V13 H1 Z M4 12 H12 V15 H4 Z"/></svg>
          608 412 7736
        </li>
        <li>
          <svg class="contact__icon" viewBox="0 0 16 16" aria-hidden="true"><path d="M1 3 H15 V13 H1 Z M2.5 4.5 V5 L8 9 L13.5 5 V4.5 Z" fill-rule="evenodd"/></svg>
          office@rwsite.com
        </li>
        <li>
          <svg class="contact__icon" viewBox="0 0 16 16" aria-hidden="true"><circle cx="8" cy="8" r="7"/><path d="M5 4 C7 5 6 7 8 8 C9 9 7 11 9 13 M10 3 C11 5 13 5 14 7" stroke="#fff" stroke-width="1.3" fill="none"/></svg>
          www.rwsite.com
        </li>
      </ul>
    </div>
  </section>

  <section class="card card--back" aria-label="Business card back">
    <p class="brand-name">R&amp;W</p>
    <p class="back-web">www.rwsite.com</p>
  </section>
</main>
</body>
</html>
```